Upstart Retirement Planning Firm needs help with business card design

Harborview Nest Advisors, LLC is looking for help with business card design. We give advice on investments, insurance, and other financial matters related to retirement. There are some required disclosures that we will provide but mostly we are looking for a professional, classy business card that reflects the theme we have chosen. We have a logo that is attached but we would like to add a phrase; "Turning Your Earned Income Into Retirement Income"

Doubled sided only so that we can add the required disclosures (needed for our industry) on the back of the card. We will provide the exact words for this in 1-2 days.

Target Market(s)

Retirees and Pre-retirees. Professionals 50+ years old

Industry/Entity Type

Financial Planning

Contact Information for Business Card

We currently have two people who will need separate cards so we'd like to have a template so that we can add names for new cards in the future.

For the first run, please show the following information.

Gregor Pelham, MBA, ChFC®, CLU®
Financial Advisor, Registered Representative
gpelham@harborviewnest.example
Phone: (555) 318-2946
Toll Free Fax: (800) 555-0193

Address is
2187 Meadowlark Ridge Rd.
Suite K418
Virginia Beach, VA 23999

Colors
3277b5

Requirements
Must have
• Logo, contact info, small phase to describe business (in description), required legal disclosures on back of the card as follows (in small font)
• Gregor Pelham is a registered representative of and offers securities through Brightmoor Capital Brokerage Corporation, Member FNQX. Brightmoor Capital Brokerage Corporation is a member of the Brightmoor Capital Alliance which is the marketing name for Brightmoor Holding Corporation and its affiliates.
Nice to have
• Rounded edges, raised letters
Should not have
• any colors that aren't in the logo (other than black for font)

```html
<!DOCTYPE html>
<html lang="en">
<head>
<meta charset="utf-8">
<title>Harborview Nest Advisors — Business Card</title>
<link rel="stylesheet" href="https://fonts.googleapis.com/css2?family=Source+Sans+3:wght@400;600&display=swap">
<style>
  :root {
    --brand-blue: #2b569a;
    --wave-grey: #a9a9a9;
    --card-white: #ffffff;
    --ink: #111111;
    --page-bg: #e4e4e4;
  }
  * { margin: 0; padding: 0; box-sizing: border-box; }
  html, body {
    width: 1189px; height: 1200px; overflow: hidden;
    background: var(--page-bg);
    font-family: "Source Sans 3", "Helvetica Neue", Arial, sans-serif;
  }
  .card {
    position: absolute; left: 140px; width: 917px; height: 523px;
    overflow: hidden;
    box-shadow: 0 6px 14px rgba(0,0,0,0.25);
  }
  .card--front { top: 46px; background: var(--card-white); }
  .card--back { top: 624px; background: var(--brand-blue); }
  .front-waves { position: absolute; inset: 0; width: 917px; height: 523px; }

  .brand {
    position: absolute; color: var(--card-white); text-align: center;
  }
  .brand-name { font-weight: 600; line-height: 1.05; }
  .brand-sub { display: block; margin-top: 10px; letter-spacing: 2px; }
  .brand-tagline { font-weight: 400; letter-spacing: 0.5px; }

  .card--front .brand { left: 40px; top: 56px; width: 440px; }
  .card--front .brand-name { font-size: 46px; }
  .card--front .brand-sub { font-size: 30px; }
  .card--front .brand-tagline {
    margin-top: 18px; padding-top: 10px; font-size: 17px;
    border-top: 1.5px solid var(--card-white);
  }

  .card--back .brand { left: 0; right: 0; top: 120px; }
  .card--back .brand-name { font-size: 66px; }
  .card--back .brand-sub { font-size: 42px; }
  .card--back .brand-tagline {
    display: inline-block; margin-top: 22px; padding-top: 12px; font-size: 24px;
    border-top: 1.5px solid var(--card-white);
  }

  .disclosure {
    position: absolute; left: 70px; right: 70px; bottom: 34px;
    color: var(--card-white); font-size: 14px; line-height: 20px; text-align: center;
  }

  .person {
    position: absolute; right: 36px; top: 52px; text-align: right; color: var(--ink);
  }
  .person__name { font-size: 42px; font-weight: 400; line-height: 1.05; margin-bottom: 4px; }
  .person__role { font-size: 27px; line-height: 32px; }
  .person__role sup { font-size: 13px; }

  .contact {
    position: absolute; right: 34px; top: 340px; list-style: none;
    color: var(--ink); font-size: 27px;
  }
  .contact li {
    display: flex; justify-content: flex-end; align-items: center;
    height: 32px; gap: 26px;
  }
  .contact svg { width: 19px; height: 19px; flex: none; }
</style>
</head>
<body>

<section class="card card--front" aria-label="Business card front">
  <svg class="front-waves" viewBox="0 0 917 523" aria-hidden="true">
    <path fill="var(--wave-grey)" d="M0,0 H917 V300 C860,276 790,252 690,250 C560,250 420,298 260,322 C170,332 90,322 0,306 Z"/>
    <path fill="var(--brand-blue)" d="M0,0 H917 V292 C860,268 780,244 690,236 C560,225 420,265 260,285 C170,295 90,285 0,262 Z"/>
  </svg>

  <div class="brand">
    <div class="brand-name">Harborview Nest<span class="brand-sub">Advisors, LLC</span></div>
    <p class="brand-tagline">Turning Your Earned Income Into Retirement Income</p>
  </div>

  <div class="person">
    <h1 class="person__name">Gregor Pelham</h1>
    <p class="person__role">MBA, ChFC<sup>®</sup>, CLU<sup>®</sup></p>
    <p class="person__role">Financial Advisor,</p>
    <p class="person__role">Registered Representative</p>
  </div>

  <ul class="contact">
    <li>(555) 318-2946
      <svg viewBox="0 0 20 20" aria-label="Phone"><rect width="20" height="20" fill="#111"/><path fill="#fff" d="M6 3 L9 6 L7.5 8 C8.5 10 10 11.5 12 12.5 L14 11 L17 14 L15 17 C10 17 3 10 3 5 Z"/></svg>
    </li>
    <li>(800) 555-0193
      <svg viewBox="0 0 20 20" aria-label="Fax"><rect width="20" height="20" fill="#111"/><rect x="6" y="3" width="8" height="4" fill="#fff"/><rect x="3" y="8" width="14" height="6" fill="#fff"/><rect x="6" y="12" width="8" height="5" fill="#fff" stroke="#111" stroke-width="1"/></svg>
    </li>
    <li>gpelham@harborviewnest.example
      <svg viewBox="0 0 20 20" aria-label="Email"><rect width="20" height="20" fill="#111"/><rect x="3" y="5" width="14" height="10" fill="#fff"/><path d="M3 5 L10 11 L17 5" fill="none" stroke="#111" stroke-width="1.3"/></svg>
    </li>
    <li>2187 Meadowlark Ridge Rd. Suite K418 Virginia Beach, VA 23999
      <svg viewBox="0 0 20 20" aria-label="Address"><rect width="20" height="20" fill="#111"/><path fill="#fff" d="M10 3 L17 10 H15 V16 H11.5 V12 H8.5 V16 H5 V10 H3 Z"/></svg>
    </li>
  </ul>
</section>

<section class="card card--back" aria-label="Business card back">
  <div class="brand">
    <div class="brand-name">Harborview Nest<span class="brand-sub">Advisors, LLC</span></div>
    <p class="brand-tagline">Turning Your Earned Income Into Retirement Income</p>
  </div>
  <p class="disclosure">Gregor Pelham is a registered representative of and offers securities through Brightmoor Capital Brokerage Corporation, Member FNQX. Brightmoor Capital Brokerage Corporation is a member of the Brightmoor Capital Alliance which is the marketing name for Brightmoor Holding Corporation and its affiliates.</p>
</section>

</body>
</html>
```